Brightmill Data Works

Our company is about IT hardwares and IT solutions. IT hardware such as PC, RAMS, storage and servers. IT solutions such as project management, BA. We are also selling new technology too.

Target Market(s)

Consumer, Small to Medium Business, Corporate

Requirements
Must have
• The business card must have the following:
• Name:
• Title:
• Contact Number:
• Email address:
• Website:
• Color: Must match the logo color upgrade

```html
<!DOCTYPE html>
<html lang="en">
<head>
<meta charset="UTF-8">
<title>Brightmill Data Works — Business Card</title>
<link rel="stylesheet" href="https://fonts.googleapis.com/css2?family=Rajdhani:wght@600;700&family=Roboto:wght@400&display=swap">
<style>
  :root {
    --page-bg: #e4e4e4;
    --card-white: #f7f7f7;
    --ink-dark: #444546;
    --ink-body: #4a4a4a;
    --brand-orange: #cd8230;
    --orange-light: #d3893a;
    --orange-deep: #bb6227;
    --white: #ffffff;
  }
  * { margin: 0; padding: 0; box-sizing: border-box; }
  html, body {
    width: 1200px;
    height: 960px;
    overflow: hidden;
    background: var(--page-bg);
  }
  .canvas {
    position: relative;
    width: 1200px;
    height: 960px;
  }
  .card {
    position: absolute;
    width: 601px;
    height: 331px;
  }
  .card--front {
    left: 314px;
    top: 113px;
    background: var(--card-white);
  }
  .card--back {
    left: 311px;
    top: 472px;
    height: 343px;
    background: radial-gradient(ellipse at 50% 42%, var(--orange-light) 0%, #c8782f 45%, var(--orange-deep) 100%);
  }

  /* front: brand block */
  .brand {
    position: absolute;
    left: 0;
    width: 366px;
    top: 108px;
    text-align: center;
  }
  .brand__mark {
    display: block;
    width: 18px;
    height: 18px;
    margin: 0 auto 14px;
    background: var(--brand-orange);
  }
  .brand__name {
    font-family: "Rajdhani", sans-serif;
    font-weight: 700;
    font-size: 36px;
    line-height: 34px;
    letter-spacing: 0.5px;
    color: var(--ink-dark);
  }

  .divider {
    position: absolute;
    left: 324px;
    top: 103px;
    width: 2px;
    height: 135px;
    background: var(--brand-orange);
  }

  /* front: person + contact */
  .person {
    position: absolute;
    left: 356px;
    top: 104px;
  }
  .person__name {
    font-family: "Rajdhani", sans-serif;
    font-weight: 600;
    font-size: 29px;
    line-height: 32px;
    color: var(--brand-orange);
  }
  .person__title {
    font-family: "Rajdhani", sans-serif;
    font-weight: 700;
    font-size: 16px;
    letter-spacing: 0.5px;
    color: var(--ink-dark);
    margin-top: 2px;
  }
  .contact {
    list-style: none;
    margin-top: 22px;
  }
  .contact__item {
    display: flex;
    align-items: center;
    gap: 7px;
    font-family: "Roboto", sans-serif;
    font-size: 14.5px;
    line-height: 19px;
    color: var(--ink-body);
  }
  .contact__icon {
    width: 12px;
    height: 12px;
    flex: none;
  }

  /* back */
  .back-brand {
    position: absolute;
    left: 0;
    right: 0;
    top: 118px;
    text-align: center;
  }
  .back-brand__mark {
    display: block;
    width: 20px;
    height: 20px;
    margin: 0 auto 16px;
    background: var(--white);
  }
  .back-brand__name {
    font-family: "Rajdhani", sans-serif;
    font-weight: 700;
    font-size: 40px;
    line-height: 38px;
    letter-spacing: 0.5px;
    color: var(--white);
  }
  .back-web {
    position: absolute;
    left: 0;
    right: 0;
    top: 292px;
    text-align: center;
    font-family: "Roboto", sans-serif;
    font-size: 13.5px;
    letter-spacing: 3.2px;
    color: var(--white);
  }
</style>
</head>
<body>
<main class="canvas">

  <section class="card card--front" aria-label="Business card front">
    <div class="brand">
      <span class="brand__mark"></span>
      <div class="brand__name">BRIGHTMILL<br>DATA WORKS</div>
    </div>

    <div class="divider"></div>

    <div class="person">
      <h1 class="person__name">DANIEL MERCER</h1>
      <p class="person__title">CEO/FOUNDER</p>
      <ul class="contact">
        <li class="contact__item">
          <svg class="contact__icon" viewBox="0 0 24 24" aria-hidden="true"><path fill="#cd8230" d="M6.6 10.8c1.4 2.8 3.8 5.1 6.6 6.6l2.2-2.2c.3-.3.7-.4 1-.2 1.1.4 2.3.6 3.6.6.6 0 1 .4 1 1V20c0 .6-.4 1-1 1C10.6 21 3 13.4 3 4c0-.6.4-1 1-1h3.5c.6 0 1 .4 1 1 0 1.3.2 2.5.6 3.6.1.3 0 .7-.2 1l-2.3 2.2z"/></svg>
          555 014 2290
        </li>
        <li class="contact__item">
          <svg class="contact__icon" viewBox="0 0 24 24" aria-hidden="true"><rect x="2" y="5" width="20" height="14" fill="#cd8230"/><path d="M2 6l10 7 10-7" fill="none" stroke="#f7f7f7" stroke-width="1.8"/></svg>
          daniel@brightmill.com
        </li>
        <li class="contact__item">
          <svg class="contact__icon" viewBox="0 0 24 24" aria-hidden="true"><circle cx="12" cy="12" r="10" fill="#cd8230"/><path d="M2 12h20M12 2c3 3 3 17 0 20M12 2c-3 3-3 17 0 20" fill="none" stroke="#f7f7f7" stroke-width="1.5"/></svg>
          www.brightmill.com
        </li>
      </ul>
    </div>
  </section>

  <section class="card card--back" aria-label="Business card back">
    <div class="back-brand">
      <span class="back-brand__mark"></span>
      <div class="back-brand__name">BRIGHTMILL DATA WORKS</div>
    </div>
    <p class="back-web">www.brightmill.com</p>
  </section>

</main>
</body>
</html>
```